Looking for Web Design for NFT project

We are an animal charity company and we are looking for a web designer for our latest NFT project. We need a custom designed single page web site structured in a specific way: about us section, how to buy our nft explanation, roadmap etc. It is strongly required the theme of the website to emphasize the Chinese culture. We insist on this since the animals on the NFTs have chinese descent.

Here are good examples of similar websites in terms of how the web page should be structured:

https://quillfernharbor.com/#/home
https://wobblets.io/
https://tarvelinplay.com/
https://mossgarland.rip/

The structure of our website should be similar to the websites listed above, however, the theme the web page should be original, more playful than serious, colourful, it should be fun and in chinese thematic. The NFTs will be 100x100 pixel 16bit animals.

Target markets: Cryptocurrency and NFT collectors/creators

Target Market(s)

Cryptocurrency and NFT collectors/creators

Industry/Entity Type

NFT Space

Coding

Coded - Design and coding required

Number of Pages Required

1 page

Requirements
Must have
• Chinese thematics / Pekingese dog breed oriented
Nice to have
• The NFTs will be 100x100 pixel pekingese dogs
Should not have
• Anything that is directly related to crypto

```html
<!DOCTYPE html>
<html lang="en">
<head>
<meta charset="utf-8">
<title>Lantern NFT</title>
<link rel="stylesheet" href="https://fonts.googleapis.com/css2?family=Titan+One&family=Barlow+Condensed:wght@300;400;500&display=swap">
<style>
:root{
  --red:#a60d1f;
  --ink:#1c171b;
  --pink:#f5e2e5;
  --pink-2:#f0dadd;
  --card:#f6e4e6;
  --muted:#6f5e62;
  --white:#ffffff;
  --tan:#9b8464;
}
*{box-sizing:border-box;margin:0;padding:0}
html,body{width:1200px;height:3009px;overflow:hidden}
body{font-family:"Barlow Condensed",sans-serif;color:var(--ink);background:var(--pink);position:relative}
.display{font-family:"Titan One",sans-serif;text-transform:uppercase;letter-spacing:1px}
.accent{color:var(--red)}
.abs{position:absolute}
.btn{position:absolute;display:flex;align-items:center;justify-content:center;border-radius:4px;font-size:16px;text-transform:uppercase;background:var(--red);color:var(--white)}

.site-header{position:absolute;left:0;top:0;width:1200px;height:94px;background:var(--pink)}
.logo{position:absolute;left:111px;top:31px;font-size:27px;color:var(--red)}
.nav{position:absolute;left:391px;top:0;height:94px;display:flex}
.nav a{display:flex;align-items:center;justify-content:center;height:94px;font-size:15px;text-transform:uppercase;color:var(--ink);text-decoration:none;border-right:1px solid #d9c4c8}
.nav a.active{background:var(--red);color:var(--white);border-right:none}
.social-dot{position:absolute;width:16px;height:16px;border-radius:50%;background:var(--red)}

.hero{position:absolute;left:0;top:94px;width:1200px;height:600px}
.hero-art{position:absolute;inset:0;background:linear-gradient(180deg,#efc9a8 0%,#ecb98e 45%,#d98d5a 75%,#c9754a 100%)}
.hero-title{position:absolute;left:0;width:1200px;top:203px;text-align:center;font-size:40px}
.hero-text{position:absolute;left:360px;width:480px;top:262px;text-align:center;font-size:17px;line-height:26px;color:#3a2a24}

.about{position:absolute;left:0;top:694px;width:1200px;height:588px;background:var(--pink)}
.about-main{position:absolute;left:111px;top:96px;width:342px;height:385px;background:#e2d2bf}
.about-frame{position:absolute;left:320px;top:298px;width:264px;height:191px;background:#f4e6e6}
.about-inner{position:absolute;left:9px;top:8px;width:246px;height:175px;background:#cbbfa2}
.section-title{font-size:29px}
.copy{font-size:16.5px;line-height:27px;text-align:justify;color:#3c3336}

.howto{position:absolute;left:0;top:1282px;width:1200px;height:470px}
.howto-panel{position:absolute;left:0;top:0;width:600px;height:470px;background:var(--red)}
.howto-art{position:absolute;left:600px;top:0;width:600px;height:470px;background:radial-gradient(ellipse at 50% 50%,#d7a36a 0%,#b88c5d 45%,var(--tan) 75%)}

.roadmap{position:absolute;left:0;top:1752px;width:1200px;height:530px;background:var(--pink)}
.step-title{position:absolute;width:200px;text-align:center;font-family:"Titan One",sans-serif;font-size:17px}
.step-text{position:absolute;width:180px;text-align:center;font-size:14px;line-height:21px;font-weight:300;color:var(--muted)}

.faq{position:absolute;left:0;top:2282px;width:1200px;height:522px;background:var(--pink-2)}
.faq-item{position:absolute;left:218px;width:763px;background:var(--card);box-shadow:0 1px 4px rgba(90,40,50,.18);border-radius:2px}
.faq-q{position:absolute;left:17px;top:15px;font-size:17px}
.faq-sign{position:absolute;right:18px;top:14px;font-size:22px;font-weight:500;color:var(--red);line-height:20px}
.faq-a{position:absolute;left:18px;top:52px;width:720px;font-size:15px;line-height:24px;color:var(--muted)}

.site-footer{position:absolute;left:0;top:2804px;width:1200px;height:205px;background:var(--ink);color:var(--white)}
.foot-logo{position:absolute;left:111px;top:50px;font-size:31px;color:var(--red)}
.foot-links{position:absolute;left:111px;top:104px;font-size:15px;display:flex;gap:14px}
.foot-social{position:absolute;top:71px;width:36px;height:36px;border-radius:50%;border:2px solid var(--white)}
</style>
</head>
<body>

<header class="site-header">
  <div class="logo display">Lantern NFT</div>
  <nav class="nav">
    <a class="active" href="#" style="width:89px">Home</a>
    <a href="#" style="width:92px">About</a>
    <a href="#" style="width:124px">How to buy</a>
    <a href="#" style="width:113px">Roadmap</a>
  </nav>
  <div class="btn" style="left:853px;top:26px;width:111px;height:47px">Join now</div>
  <span class="social-dot" style="left:1003px;top:41px" role="img" aria-label="social link"></span>
  <span class="social-dot" style="left:1036px;top:41px" role="img" aria-label="social link"></span>
  <span class="social-dot" style="left:1072px;top:41px" role="img" aria-label="social link"></span>
</header>

<section class="hero">
  <div class="hero-art" role="img" aria-label="Illustrated festive scene with red paper lanterns, clouds, rolling hills and a Pekingese dog"></div>
  <h1 class="hero-title display">Welcome to <span class="accent">Lantern NFT</span></h1>
  <p class="hero-text">Lorem ipsum dolor sit amet, consectetur adipiscing elit, sed do eiu smod tempor et dolore magna aliqua.</p>
  <div class="btn" style="left:544px;top:338px;width:111px;height:47px">Buy a NFT</div>
</section>

<section class="about">
  <div class="about-main" role="img" aria-label="Illustrated Pekingese dog portrait"></div>
  <div class="about-frame"><div class="about-inner" role="img" aria-label="Illustrated sitting Pekingese dog"></div></div>
  <h2 class="section-title display abs" style="left:647px;top:110px">About <span class="accent">Lantern NFT</span></h2>
  <p class="copy abs" style="left:647px;top:174px;width:441px">Lorem ipsum dolor sit amet, consectetur adipiscing elit, sed do eiusmod tem por incididunt ut labore et dolore magna aliqua. Ut enim ad minim veniam, quis nostrud exercitation ullamco laboris nisi ut aliquip ex ea commodo consequat.</p>
  <p class="copy abs" style="left:647px;top:309px;width:441px">Labore et dolore magna aliqua. Ut enim ad minim veniam, quis nostrud exercitation ullamco laboris nisi ut aliquip ex ea commodo consequat. Duis aute irure dolor in reprehenderitea.</p>
  <div class="btn" style="left:648px;top:413px;width:120px;height:47px">Learn more</div>
</section>

<section class="howto">
  <div class="howto-panel">
    <h2 class="section-title display abs" style="left:111px;top:58px;color:var(--white)">How to buy our NFT</h2>
    <p class="copy abs" style="left:111px;top:122px;width:441px;color:var(--white)">Lorem ipsum dolor sit amet, consectetur adipiscing elit, sed do eiusmod tem por incididunt ut labore et dolore magna aliqua. Ut enim ad minim veniam, quis nostrud exercitation ullamco laboris nisi ut aliquip ex ea commodo consequat.</p>
    <p class="copy abs" style="left:111px;top:257px;width:441px;color:var(--white)">Labore et dolore magna aliqua. Ut enim ad minim veniam, quis nostrud exercitation ullamco laboris nisi ut aliquip ex ea commodo consequat. Duis aute irure dolor in reprehenderitea.</p>
    <div class="btn" style="left:112px;top:360px;width:120px;height:47px;background:var(--white);color:var(--red)">Buy a NFT</div>
  </div>
  <div class="howto-art" role="img" aria-label="Detailed illustrated Pekingese dog head"></div>
</section>

<section class="roadmap">
  <h2 class="display abs" style="left:0;width:1200px;top:92px;text-align:center;font-size:30px">Roadmap</h2>
  <svg class="abs" style="left:0;top:0" width="1200" height="530" aria-hidden="true">
    <line x1="111" y1="306" x2="1088" y2="306" stroke="#a60d1f" stroke-width="1.5"/>
    <g font-family="Titan One, sans-serif" font-size="22" text-anchor="middle" fill="#fff">
      <line x1="201" y1="234" x2="201" y2="306" stroke="#a60d1f" stroke-width="1.5"/>
      <circle cx="201" cy="234" r="34" fill="#a60d1f"/><text x="201" y="242">01</text>
      <line x1="600" y1="234" x2="600" y2="306" stroke="#a60d1f" stroke-width="1.5"/>
      <circle cx="600" cy="234" r="34" fill="#a60d1f"/><text x="600" y="242">03</text>
      <line x1="999" y1="234" x2="999" y2="306" stroke="#a60d1f" stroke-width="1.5"/>
      <circle cx="999" cy="234" r="34" fill="#a60d1f"/><text x="999" y="242">05</text>
      <line x1="401" y1="306" x2="401" y2="376" stroke="#1c171b" stroke-width="1.5"/>
      <circle cx="401" cy="376" r="34" fill="#1c171b"/><text x="401" y="384">02</text>
      <line x1="799" y1="306" x2="799" y2="376" stroke="#1c171b" stroke-width="1.5"/>
      <circle cx="799" cy="376" r="34" fill="#1c171b"/><text x="799" y="384">04</text>
    </g>
    <g fill="#fff" stroke-width="5">
      <circle cx="201" cy="306" r="9" stroke="#a60d1f"/>
      <circle cx="401" cy="306" r="9" stroke="#1c171b"/>
      <circle cx="600" cy="306" r="9" stroke="#a60d1f"/>
      <circle cx="799" cy="306" r="9" stroke="#1c171b"/>
      <circle cx="999" cy="306" r="9" stroke="#a60d1f"/>
    </g>
  </svg>
  <div class="step-title" style="left:301px;top:172px">Marketplace</div>
  <p class="step-text" style="left:311px;top:205px">Sed ut perspiciatis unde omnis is te natus error sit voluptatem accu santium dolorem.</p>
  <div class="step-title" style="left:699px;top:172px">Airdrops</div>
  <p class="step-text" style="left:709px;top:205px">Sed ut perspiciatis unde omnis is te natus error sit voluptatem accu santium dolorem.</p>
  <div class="step-title accent" style="left:101px;top:337px">Launch</div>
  <p class="step-text" style="left:111px;top:370px">Sed ut perspiciatis unde omnis is te natus error sit voluptatem accu santium dolorem.</p>
  <div class="step-title accent" style="left:500px;top:337px">Analytics</div>
  <p class="step-text" style="left:510px;top:370px">Sed ut perspiciatis unde omnis is te natus error sit voluptatem accu santium dolorem.</p>
  <div class="step-title accent" style="left:899px;top:337px">Deliver</div>
  <p class="step-text" style="left:909px;top:370px">Sed ut perspiciatis unde omnis is te natus error sit voluptatem accu santium dolorem.</p>
</section>

<section class="faq">
  <h2 class="display abs" style="left:0;width:1200px;top:48px;text-align:center;font-size:23px"><span class="accent">Frequently</span> asked questions</h2>
  <div class="faq-item" style="top:111px;height:110px">
    <div class="faq-q">What Is Lantern NFT?</div><div class="faq-sign">&minus;</div>
    <p class="faq-a">Sed ut perspiciatis unde omnis iste natus error sit voluptatem accusantium doloremque laudantium, totam rem aperi am, eaque ipsa quae ab illo inventore veritatis et quasi architectoea.</p>
  </div>
  <div class="faq-item" style="top:233px;height:51px"><div class="faq-q">Lorem ipsum dolor sit amet, consectetur adipiscing elit, sed do?</div><div class="faq-sign">+</div></div>
  <div class="faq-item" style="top:295px;height:51px"><div class="faq-q">Lorem ipsum dolor sit adipiscing elit, sed do?</div><div class="faq-sign">+</div></div>
  <div class="faq-item" style="top:355px;height:51px"><div class="faq-q">Lorem ipsum dolor sit amet, consectetur adipiscing &nbsp;do?</div><div class="faq-sign">+</div></div>
  <div class="faq-item" style="top:417px;height:51px"><div class="faq-q">Lorem ipsum dolor sit amet, consectetpiscing elit, sed do?</div><div class="faq-sign">+</div></div>
</section>

<footer class="site-footer">
  <div class="foot-logo display">Lantern NFT</div>
  <nav class="foot-links"><span>HOME</span><span>|</span><span>ABOUT</span><span>|</span><span>HOW TO BUY</span><span>|</span><span>ROADMAP</span></nav>
  <span class="foot-social" style="left:967px;background:var(--white)" role="img" aria-label="social link"></span>
  <span class="foot-social" style="left:1009px" role="img" aria-label="social link"></span>
  <span class="foot-social" style="left:1052px" role="img" aria-label="social link"></span>
  <div class="abs" style="left:111px;top:145px;width:977px;height:1px;background:#4a4247"></div>
  <p class="abs" style="left:0;width:1200px;top:160px;text-align:center;font-size:13px">&copy;2022 &ndash; ALL RIGHTS RESERVED BY <strong>LANTERN NFT</strong></p>
</footer>

</body>
</html>
```